Kelvor Engineers: Why you should hire us keepsake

New design. Open to plastic cards. We are an engineering firm that designs cell phone towers and commercial buildings. Please check out our website www.kelvorstruct.com for more details. We want people to remember our card and for it to be useful if possible. We want the same look and feel on these cards to be translated to other marketing material we may need such as brochures.

Target Market(s)

Architects, Developers and Telecommunication Carriers

Industry/Entity Type

Engineering

Contact Information for Business Card

Card with our company colors, logo, and innovative design with elements related to our industry.

Font styles to use
Sans Serif

Colors
9bcb3c
abd036
0255a3

Requirements
Must have
• Sleek and hip design
Nice to have
• Bright lime green and navy coloring that pops with an innovative design.
Should not have
• A basic and boring design

```html
<!DOCTYPE html>
<html lang="en">
<head>
<meta charset="utf-8">
<title>Kelvor Engineers – Business Card</title>
<link rel="stylesheet" href="https://fonts.googleapis.com/css2?family=Roboto:wght@400;500;700;900&display=swap">
<style>
  :root {
    --lime: #cdd32a;
    --navy: #1d3567;
    --white: #ffffff;
    --ink-soft: #3b4a6b;
    --backdrop: #2a2a2a;
  }
  * { margin: 0; padding: 0; box-sizing: border-box; }
  html, body { width: 1200px; height: 930px; overflow: hidden; }
  body {
    background: var(--backdrop);
    font-family: "Roboto", Arial, sans-serif;
    position: relative;
  }
  .card {
    position: absolute;
    width: 560px;
    height: 320px;
    border-radius: 18px;
    overflow: hidden;
  }

  /* Front */
  .card-front {
    left: 50px; top: 110px;
    background: var(--lime);
  }
  .card-front .brand {
    position: absolute;
    left: 0; right: 0; top: 104px;
    text-align: center;
    color: var(--white);
    font-weight: 900;
    font-size: 58px;
    letter-spacing: -1px;
    line-height: 1;
  }
  .card-front .offices {
    position: absolute;
    left: 0; right: 0; bottom: 34px;
    text-align: center;
    color: var(--white);
    font-weight: 500;
    font-size: 17px;
    letter-spacing: 1.5px;
  }
  .offices .sep { margin: 0 8px; opacity: 0.9; }

  /* Back */
  .card-back {
    left: 590px; top: 500px;
    background: var(--white);
  }
  .card-back .brand {
    position: absolute;
    left: 34px; top: 54px;
    color: var(--lime);
    font-weight: 900;
    font-size: 32px;
    letter-spacing: -0.5px;
    line-height: 1;
  }
  .person {
    position: absolute;
    right: 40px; top: 44px;
    text-align: right;
    width: 190px;
    border-bottom: 1.5px solid var(--navy);
    padding-bottom: 6px;
  }
  .person-name {
    color: var(--navy);
    font-weight: 700;
    font-size: 22px;
  }
  .person-title {
    color: var(--lime);
    font-size: 14px;
    margin-top: 1px;
  }
  .divider {
    position: absolute;
    left: 34px; top: 170px;
    width: 230px;
    border-top: 1.5px solid var(--navy);
  }
  .contacts {
    position: absolute;
    left: 34px; top: 182px;
    list-style: none;
    color: var(--ink-soft);
    font-size: 15px;
    line-height: 21px;
  }
  .contacts li { display: flex; align-items: center; gap: 10px; }
  .contacts svg { width: 11px; height: 11px; flex: none; }
  .tagline {
    position: absolute;
    right: 36px; top: 214px;
    color: var(--navy);
    font-weight: 500;
    font-size: 14px;
    letter-spacing: 0.5px;
  }
  .base-rule {
    position: absolute;
    left: 0; right: 0; bottom: 18px;
    height: 4px;
    background: var(--lime);
  }
  .base-band {
    position: absolute;
    left: 0; right: 0; bottom: 0;
    height: 12px;
    background: var(--navy);
  }
</style>
</head>
<body>

<section class="card card-front" aria-label="Card front">
  <div class="brand">Kelvor Engineers</div>
  <div class="offices">DENVER<span class="sep">|</span>PHOENIX<span class="sep">|</span>TAMPA<span class="sep">|</span>RALEIGH</div>
</section>

<section class="card card-back" aria-label="Card back">
  <div class="brand">Kelvor Engineers</div>

  <div class="person">
    <div class="person-name">Dana Whitlow</div>
    <div class="person-title">Director</div>
  </div>

  <div class="divider"></div>

  <ul class="contacts">
    <li>
      <svg viewBox="0 0 12 12"><path d="M3 1l2 2-1 1.5c.6 1.4 1.6 2.4 3 3L8.5 6.5l2 2-1.3 1.8C5.5 10 2 6.5 1.7 2.8z" fill="#cdd32a"/></svg>
      555.201.4410
    </li>
    <li>
      <svg viewBox="0 0 12 12"><rect x="3" y="1" width="6" height="10" rx="1" fill="none" stroke="#cdd32a" stroke-width="1.4"/></svg>
      555.201.7723
    </li>
    <li>
      <svg viewBox="0 0 12 12"><rect x="1" y="2.5" width="10" height="7" fill="none" stroke="#cdd32a" stroke-width="1.3"/><path d="M1 2.5l5 4 5-4" fill="none" stroke="#cdd32a" stroke-width="1.3"/></svg>
      dwhitlow@kelvorstruct.com
    </li>
    <li>
      <svg viewBox="0 0 12 12"><circle cx="6" cy="6" r="5" fill="#cdd32a"/></svg>
      www.kelvorstruct.com
    </li>
  </ul>

  <div class="tagline">MULTI-DISCIPLINE ENGINEERING</div>

  <div class="base-rule"></div>
  <div class="base-band"></div>
</section>

</body>
</html>
```